I need a business card designed using the logo provided either vertical or horizontal......Harbourline Property Group is an Australian based real estate company that caters for the upper end of the market so the design of the business card "must reflect" the companies image!!
Colour combinations are optional but "must be realistic" and must be able to be accurately useable CMYK colours.
Please consider that any colours used "must be able to be used" and be suitable in following designs for "pull out banner signs" and "real estate signs".
The colours and the font in the attached designs are for example and other combinations are encouraged.
Target Market(s)
The High End of the Australian real estate market
Industry/Entity Type
Business
Contact Information for Business Card
Logo - Business Name - Director + Licensed Real Estate Agent - Mobile Number (Cell Phone) - Business Number - Fax - Email Address - Web address
Requirements
Must have
- Designs and colours (CMYK) that can easily be interpreted by an Australian printer.
Nice to have
- Some alternative ideas on colour and font..........the ones provided are ok and have been provided as an example but I am looking for alternative ideas
Should not have
- Loud, overly bright colours. Designs that do not reflect the professional standards of the business.
- Designs that look good on a computer monitor but can not be re-created on a printing press.............this is most important when it comes to shading etc.

```html
<!DOCTYPE html>
<html lang="en">
<head>
<meta charset="utf-8">
<title>Harbourline Property Group – Business Card</title>
<link rel="stylesheet" href="https://fonts.googleapis.com/css2?family=Mulish:wght@400;500;700&display=swap">
<style>
  :root {
    --page: #ffffff;
    --teal: #588891;
    --mist: #e6e7e8;
    --white: #ffffff;
    --mark: #a9c4cc;
  }
  * { margin: 0; padding: 0; box-sizing: border-box; }
  html, body {
    width: 1200px;
    height: 500px;
    overflow: hidden;
    background: var(--page);
  }
  body {
    position: relative;
    font-family: "Mulish", sans-serif;
  }
  .card {
    position: absolute;
    top: 102px;
    width: 510px;
    height: 291px;
  }
  .card--front {
    left: 74px;
    background: var(--teal);
  }
  .card--back {
    left: 614px;
    background: var(--mist);
    display: flex;
    align-items: center;
    justify-content: center;
  }
  .brand__square {
    position: absolute;
    left: 185px;
    top: 36px;
    width: 140px;
    height: 140px;
    background: var(--mark);
  }
  .brand__name {
    position: absolute;
    left: 0;
    right: 0;
    top: 210px;
    text-align: center;
    color: var(--white);
    font-size: 23px;
    line-height: 30px;
    font-weight: 500;
    letter-spacing: 0.2px;
  }
  .contact {
    list-style: none;
    text-align: center;
    color: var(--teal);
    font-size: 20px;
    line-height: 28.5px;
    font-weight: 400;
    margin-top: 4px;
  }
  .contact strong { font-weight: 700; }
</style>
</head>
<body>
  <section class="card card--front">
    <span class="brand__square"></span>
    <span class="brand__name">Harbourline Property Group</span>
  </section>

  <section class="card card--back">
    <ul class="contact">
      <li><strong>name here</strong> director</li>
      <li><strong>000.000.0000</strong> mobile</li>
      <li><strong>000.000.0000</strong> office</li>
      <li><strong>000.000.0000</strong> fax</li>
      <li><strong>harbourlineproperty.com</strong></li>
    </ul>
  </section>
</body>
</html>
```